Debt Collection Website Design! We are the solution for landlords to get paid what they are owed.

We are a 3rd party debt collection company that specializes in Residential and Commercial real estate debt collection. We help landlords recover money from past residents by being fair, friendly and aggressive. We also collect/buy/sell/trade civil judgments won resulting from anything from automobile accidents to evictions to a pet zebra getting stolen. We buy single judgments to large portfolios, we also collect judgments for a nominal fee.

I would like a new, modern, easy to navigate website. A spot that we can post news stories or updated information about our company. I have included our company logo that must be on the top of the page. Feel free to ask any questions that will help get the process going.

Target Market(s)

Landlords, small to large apartment complex. Real estate services and lawyers.

Industry/Entity Type

Real Estate

Number of Pages Required

3 page

Requirements
Must have
• Company logo which has been attached. A page where we can explain the collection process, fees and placement. A page where we can explain judgments, collection vs. selling, placement form. I am open to any font/designs and willing to work with anyone.
Nice to have
• Nice to have a spot on the homepage to place news articles about ourselves and our industry.
Should not have
• I don't want it over crowded. Simple, sleek and easy to navigate is best. No gavels on any of the pages. It cannot look legal, say/show anything that we use legal powers to collect. We are not a law office, we don't practice law, we are 3rd party debt collection agency.

```html
<!DOCTYPE html>
<html lang="en">
<head>
<meta charset="utf-8">
<title>Castellan Recovery, LLC</title>
<link rel="stylesheet" href="https://fonts.googleapis.com/css2?family=Open+Sans:ital,wght@0,400;0,600;0,700;1,400&display=swap">
<style>
:root{
  --navy:#1f3458;
  --blue:#1f5a9a;
  --text:#555;
  --heading:#333;
  --muted:#8a8a8a;
  --line:#e3e3e3;
  --grey-band:#e4e4e4;
  --footer:#2f3338;
  --footer-bottom:#26292d;
  --footer-text:#b8bcc1;
  --white:#fff;
}
*{margin:0;padding:0;box-sizing:border-box}
html,body{width:718px;height:1200px;overflow:hidden;background:var(--white)}
body{font-family:"Open Sans",Arial,sans-serif;color:var(--text);position:relative}
.abs{position:absolute}

/* header */
.brand{left:58px;top:10px;display:flex;align-items:center;gap:7px}
.brand-mark{width:26px;height:26px;background:var(--navy)}
.brand-name{font-size:17px;font-weight:400;color:var(--navy);line-height:1;letter-spacing:.5px}
.brand-name small{display:block;font-size:10px;letter-spacing:.6px;margin-top:1px}
.contact{left:348px;top:13px;display:flex;align-items:center;gap:6px;font-size:7.5px;color:var(--muted)}
.phone-icon{width:23px;height:23px;border-radius:50%;background:var(--navy);display:flex;align-items:center;justify-content:center}
.contact b{color:var(--navy);font-weight:600}
.social{left:472px;top:16px;display:flex;align-items:center;gap:5px;font-size:6.8px;color:var(--muted)}
.social span.dot{width:16px;height:16px;border-radius:50%;display:inline-block}
.social .d1{background:#2457a8}.social .d2{background:#3aa4dc}.social .d3{background:#e28a1e}.social .d4{background:#1e6a8a}

.nav{left:0;top:47px;width:718px;height:29px;border-top:1px solid var(--line);border-bottom:1px solid var(--line);background:#fafafa}
.nav a{position:absolute;top:9px;font-size:7.6px;color:#555;text-decoration:none}
.nav a.active{color:var(--navy)}
.nav .active-bar{position:absolute;left:64px;top:26px;width:50px;height:2px;background:var(--blue)}
.nav .search{position:absolute;left:641px;top:6px;width:16px;height:16px;border-radius:50%;border:1px solid var(--line);background:#fff}

/* hero */
.hero{left:0;top:76px;width:718px;height:269px;background:linear-gradient(180deg,#6a4a38 0%,#b46a3c 35%,#8a4a28 62%,#2a1c16 100%)}
.hero-caption{left:0;top:310px;width:718px;height:35px;background:rgba(0,0,0,.45);color:#f2f2f2;font-size:9.6px;padding:10px 0 0 60px;text-transform:uppercase;letter-spacing:.1px}
.hero-caption b{font-weight:700}

/* features */
.feature{top:372px;width:200px}
.feature svg{position:absolute;left:0;top:0}
.feature h3{margin-left:42px;font-size:7.4px;font-weight:700;color:var(--heading);line-height:11px}
.feature p{margin-left:42px;font-size:6.4px;line-height:13px;margin-top:3px}

.welcome{left:0;top:468px;width:718px;text-align:center}
.welcome h2{font-size:11.4px;font-weight:700;color:var(--heading);letter-spacing:.2px}
.welcome p{width:490px;margin:9px auto 0;font-size:7.6px;line-height:14px}

.card{top:561px;width:185px}
.card .ph{height:105px}
.card h3{font-size:8px;font-weight:700;color:var(--heading);margin-top:13px}
.card p{font-size:6.4px;line-height:13px;margin-top:6px}

/* news */
.news{left:0;top:748px;width:718px;height:206px;background:var(--grey-band)}
.news h2{position:absolute;left:58px;top:23px;font-size:9.6px;font-weight:700;color:var(--navy)}
.arrows{position:absolute;left:644px;top:24px;font-size:8px;color:#999;letter-spacing:4px}
.news-item{position:absolute;top:50px;width:144px}
.news-item .ph{height:95px}
.news-item h3{font-size:6.8px;font-weight:700;color:var(--heading);margin-top:12px}
.news-item p{font-size:6.4px;margin-top:5px}

.partners{left:0;top:954px;width:718px;height:58px;display:flex;align-items:center;justify-content:space-around;padding:0 60px}
.partners span{display:block;height:20px;border-radius:3px}

/* footer */
.footer{left:0;top:1012px;width:718px;height:158px;background:var(--footer);color:var(--footer-text)}
.footer h4{position:absolute;font-size:8.6px;font-weight:400;color:#fff}
.quote{position:absolute;left:86px;top:50px;width:155px;font-size:6px;line-height:12.3px;font-style:italic}
.qmark{position:absolute;font-size:14px;color:#777;font-family:Georgia,serif}
.author{position:absolute;left:84px;top:124px;font-size:6.6px}
.author b{font-weight:700;color:#ccc}.author span{color:#6e7378}
.links{position:absolute;font-size:6.6px;line-height:13.3px;list-style:none}
.foot-brand{position:absolute;left:533px;top:58px;display:flex;align-items:center;gap:7px;color:#6b7075;opacity:.9}
.foot-brand .mk{width:28px;height:28px;background:#5d6267}
.foot-brand div{font-size:18px;line-height:1;letter-spacing:.5px}
.foot-brand small{display:block;font-size:10.5px}
.copy{left:0;top:1170px;width:718px;height:30px;background:var(--footer-bottom);color:#9ea2a7;font-size:6.6px;text-align:center;padding-top:10px}
</style>
</head>
<body>

<header>
  <div class="abs brand">
    <span class="brand-mark"></span>
    <div class="brand-name">Castellan<small>Recovery, LLC</small></div>
  </div>
  <div class="abs contact">
    <span class="phone-icon"><svg width="11" height="11" viewBox="0 0 24 24"><path fill="#fff" d="M6.6 10.8a15 15 0 0 0 6.6 6.6l2.2-2.2c.3-.3.7-.4 1-.2 1.1.4 2.3.6 3.6.6.6 0 1 .4 1 1V20c0 .6-.4 1-1 1A17 17 0 0 1 3 4c0-.6.4-1 1-1h3.5c.6 0 1 .4 1 1 0 1.3.2 2.5.6 3.6.1.3 0 .7-.2 1z"/></svg></span>
    Call Us : <b>( 2360 ) 555 014</b>
  </div>
  <div class="abs social">Connect with our social network :
    <span class="dot d1"></span><span class="dot d2"></span><span class="dot d3"></span><span class="dot d4"></span>
  </div>
  <nav class="abs nav">
    <a class="active" style="left:81px">Home</a>
    <a style="left:140px">About Us</a>
    <a style="left:210px">Services</a>
    <a style="left:273px">Debt collection</a>
    <a style="left:358px">Projects</a>
    <a style="left:421px">Events</a>
    <a style="left:478px">Contact Us</a>
    <span class="active-bar"></span>
    <span class="search"></span>
  </nav>
</header>

<section class="abs hero" role="img" aria-label="Photo of a waterfront city skyline at sunset with moored boats"></section>
<div class="abs hero-caption"><b>We are a debt collection company</b> that specializes in residential and commercial real estate debt collection.</div>

<section>
  <div class="abs feature" style="left:68px">
    <svg width="32" height="30" viewBox="0 0 32 30"><path fill="var(--navy)" d="M2 10h8a4 4 0 1 1 6 0h8v8a4 4 0 1 0 0 6v6H2z"/></svg>
    <h3>ES SIMPLEMENTE EL TEXTO DE</h3>
    <p>Es simplemente el texto de relleno de las imprentas y archivos de texto. Lorem Ipsum ha sido el texto de relleno...</p>
  </div>
  <div class="abs feature" style="left:270px">
    <svg width="32" height="30" viewBox="0 0 32 30"><rect x="1" y="2" width="30" height="20" rx="2" fill="var(--navy)"/><rect x="4" y="5" width="24" height="13" fill="#fff"/><rect x="13" y="22" width="6" height="4" fill="var(--navy)"/><rect x="9" y="26" width="14" height="2" fill="var(--navy)"/></svg>
    <h3>ES SIMPLEMENTE EL TEXTO DE</h3>
    <p>Es simplemente el texto de relleno de las imprentas y archivos de texto. Lorem Ipsum ha sido el texto de relleno...</p>
  </div>
  <div class="abs feature" style="left:485px">
    <svg width="32" height="30" viewBox="0 0 32 30"><g fill="var(--navy)"><circle cx="16" cy="6" r="4.5"/><circle cx="7" cy="9" r="3.5"/><circle cx="25" cy="9" r="3.5"/><path d="M9 26a7 7 0 0 1 14 0z"/><path d="M1 24a6 6 0 0 1 10-4v6H1zM31 24a6 6 0 0 0-10-4v6h10z"/><path d="M8 26a8 8 0 0 1 16 0z"/></g></svg>
    <h3>ES SIMPLEMENTE EL TEXTO DE</h3>
    <p>Es simplemente el texto de relleno de las imprentas y archivos de texto. Lorem Ipsum ha sido el texto de relleno...</p>
  </div>
</section>

<section class="abs welcome">
  <h2>WELCOME TO CASTELLAN RECOVERY</h2>
  <p>We are a debt collection company that specializes in Residential and Commercial real estate debt collection. We help landlords recover money from past residents by being fair, friendly and aggressive. We also collect/buy/sell/trade civil judgments won resulting from anything from automobile accidents.</p>
</section>

<section>
  <article class="abs card" style="left:59px">
    <div class="ph" role="img" aria-label="Photo of hands reviewing printed financial charts" style="background:linear-gradient(135deg,#d9dde2,#8a8f96 60%,#3a3d42)"></div>
    <h3>ES SIMPLEMENTE EL TEXTO DE</h3>
    <p>Es simplemente el texto de relleno de las imprentas y archivos de texto. Lorem Ipsum ha sido el texto de relleno</p>
  </article>
  <article class="abs card" style="left:265px">
    <div class="ph" role="img" aria-label="Photo of a business team meeting around a table" style="background:linear-gradient(135deg,#e4e6ea,#9aa0a8 55%,#3f4550)"></div>
    <h3>ES SIMPLEMENTE EL TEXTO DE</h3>
    <p>Es simplemente el texto de relleno de las imprentas y archivos de texto. Lorem Ipsum ha sido el texto de relleno</p>
  </article>
  <article class="abs card" style="left:474px">
    <div class="ph" role="img" aria-label="Photo of a city skyline at sunset over a marina" style="background:linear-gradient(180deg,#6d4a3a,#b66a3a 50%,#2c1e18)"></div>
    <h3>ES SIMPLEMENTE EL TEXTO DE</h3>
    <p>Es simplemente el texto de relleno de las imprentas y archivos de texto. Lorem Ipsum ha sido el texto de relleno</p>
  </article>
</section>

<section class="abs news">
  <h2>LATEST NEWS</h2>
  <span class="arrows">‹ ›</span>
  <article class="news-item" style="left:59px">
    <div class="ph" role="img" aria-label="Photo of two professionals shaking hands in a bright office" style="background:linear-gradient(135deg,#eef1f4,#aeb6bf 60%,#6d757e)"></div>
    <h3>ES SIMPLEMENTE EL TEXTO DE</h3><p>Posted on 27 January 2015</p>
  </article>
  <article class="news-item" style="left:211px">
    <div class="ph" role="img" aria-label="Photo of modern glass office towers" style="background:linear-gradient(180deg,#8fb3cf,#5f8aa6 55%,#3c5a4e)"></div>
    <h3>ES SIMPLEMENTE EL TEXTO DE</h3><p>Posted on 27 January 2015</p>
  </article>
  <article class="news-item" style="left:362px">
    <div class="ph" role="img" aria-label="Photo of colleagues smiling at a meeting table" style="background:linear-gradient(135deg,#e7eaee,#9ea5ad 55%,#30343a)"></div>
    <h3>ES SIMPLEMENTE EL TEXTO DE</h3><p>Posted on 27 January 2015</p>
  </article>
  <article class="news-item" style="left:514px">
    <div class="ph" role="img" aria-label="Top view photo of a team working around a laptop" style="background:linear-gradient(135deg,#b89c7e,#2c3850 55%,#1c2336)"></div>
    <h3>ES SIMPLEMENTE EL TEXTO DE</h3><p>Posted on 27 January 2015</p>
  </article>
</section>

<section class="abs partners" aria-label="Partners">
  <span style="width:56px;background:#d8d8d8"></span>
  <span style="width:46px;background:#e8c9a8"></span>
  <span style="width:30px;background:#c9dfae"></span>
  <span style="width:64px;background:#b8cce2"></span>
  <span style="width:34px;background:#b3c8db"></span>
  <span style="width:58px;background:#ddd6a8"></span>
  <span style="width:56px;background:#f2cfa3"></span>
</section>

<footer class="abs footer">
  <h4 style="left:73px;top:25px">Testimonials</h4>
  <span class="arrows" style="left:230px;top:25px;color:#888">‹ ›</span>
  <span class="qmark" style="left:71px;top:44px">“</span>
  <p class="quote">Simply dummy text of the printing and typesetting industry. Lorem Ipsum has been the industry's standard dummy text ever since the 1500s, when an unknown printer took a galley of type and scrambled it to make a type specimen book...</p>
  <span class="qmark" style="left:235px;top:103px">”</span>
  <p class="author"><b>MARCUS HALE</b> <span>Marketing Executive</span></p>

  <h4 style="left:316px;top:25px">Welcome</h4>
  <ul class="links" style="left:316px;top:45px">
    <li>Home</li><li>About Us</li><li>Services</li><li>Debt collection</li><li>&nbsp;Projects</li><li>Events</li><li>Contact Us</li>
  </ul>
  <h4 style="left:427px;top:25px">information</h4>
  <ul class="links" style="left:427px;top:45px">
    <li>Privacy Policy</li><li>Terms &amp; Conditions</li><li>Sitemap</li>
  </ul>
  <div class="foot-brand"><span class="mk"></span><div>Castellan<small>Recovery, LLC</small></div></div>
</footer>
<div class="abs copy">© 2015. Castellan. All rights reserved.</div>

</body>
</html>
```